Veldmark Supplies Business Card

Professional business card that stand out to our potential customers. Front and back with clean modern design

Industry/Entity Type

Oil and gas

Contact Information for Business Card

Name, address, website , office phone and cell number

Requirements
Must have
• Editable files for each employee

```html
<!DOCTYPE html>
<html lang="en">
<head>
<meta charset="utf-8">
<title>Veldmark Supplies Business Card</title>
<link href="https://fonts.googleapis.com/css2?family=Montserrat:wght@400;500;800&display=swap" rel="stylesheet">
<style>
  :root {
    --brand-red: #ff0000;
    --brand-blue: #00acd0;
    --paper: #ffffff;
    --backdrop: #ecebe8;
    --shadow: rgba(0, 0, 0, 0.18);
  }
  * { box-sizing: border-box; margin: 0; padding: 0; }
  html, body {
    width: 1200px;
    height: 878px;
    overflow: hidden;
    background: var(--backdrop);
    font-family: "Montserrat", sans-serif;
  }
  .canvas {
    position: relative;
    width: 1200px;
    height: 878px;
    display: flex;
    justify-content: center;
    align-items: center;
    gap: 80px;
  }
  .card {
    position: relative;
    width: 360px;
    height: 580px;
    border-radius: 34px;
    overflow: hidden;
    background: var(--brand-red);
    box-shadow: 0 14px 30px var(--shadow);
    color: var(--paper);
  }

  /* Back side */
  .card--back .brand-mark {
    position: absolute;
    left: 50%;
    top: 50%;
    transform: translate(-50%, -50%) rotate(-90deg);
    display: flex;
    align-items: center;
    gap: 18px;
    white-space: nowrap;
  }
  .card--back .brand-square {
    width: 34px;
    height: 34px;
    background: var(--paper);
  }
  .card--back .brand-name {
    font-weight: 800;
    font-size: 34px;
    letter-spacing: 2px;
    text-transform: uppercase;
    color: var(--paper);
  }

  /* Front side */
  .card--front .split {
    position: absolute;
    inset: 0;
    width: 100%;
    height: 100%;
  }
  .card--front .brand-name {
    position: absolute;
    top: 34px;
    left: 0;
    right: 0;
    text-align: center;
    font-weight: 800;
    font-size: 25px;
    letter-spacing: 1.5px;
    text-transform: uppercase;
    color: var(--brand-red);
  }
  .card--front .brand-square {
    position: absolute;
    top: 98px;
    left: 50%;
    width: 120px;
    height: 120px;
    transform: translateX(-50%);
    background: var(--brand-blue);
    border: 6px solid var(--paper);
    outline: 4px solid var(--brand-red);
  }
  .person {
    position: absolute;
    top: 262px;
    left: 0;
    right: 0;
    text-align: center;
  }
  .person__name {
    font-weight: 800;
    font-size: 26px;
    letter-spacing: 0.5px;
    text-transform: uppercase;
  }
  .person__role {
    display: flex;
    align-items: center;
    justify-content: center;
    gap: 12px;
    margin-top: 2px;
    font-weight: 500;
    font-size: 15px;
  }
  .person__role::before,
  .person__role::after {
    content: "";
    width: 70px;
    height: 1.5px;
    background: var(--paper);
  }
  .contact-icons {
    position: absolute;
    top: 346px;
    left: 0;
    right: 0;
    display: flex;
    justify-content: center;
    gap: 14px;
  }
  .contact-icons svg {
    width: 28px;
    height: 28px;
    display: block;
  }
  .contact-list {
    position: absolute;
    top: 392px;
    left: 0;
    right: 0;
    text-align: center;
    font-size: 14.5px;
    line-height: 1.4;
    font-weight: 500;
  }
  .divider {
    width: 230px;
    height: 1.5px;
    margin: 12px auto;
    background: var(--paper);
  }
  .address {
    font-size: 14.5px;
  }
</style>
</head>
<body>
<main class="canvas">

  <section class="card card--back" aria-label="Card back">
    <div class="brand-mark">
      <span class="brand-square"></span>
      <span class="brand-name">Veldmark Supplies</span>
    </div>
  </section>

  <section class="card card--front" aria-label="Card front">
    <svg class="split" viewBox="0 0 360 580" preserveAspectRatio="none" aria-hidden="true">
      <rect width="360" height="580" fill="var(--brand-red)"/>
      <polygon points="0,0 360,0 360,110 0,250" fill="var(--paper)"/>
    </svg>

    <div class="brand-name">Veldmark Supplies</div>
    <div class="brand-square"></div>

    <div class="person">
      <div class="person__name">Dren Halloway</div>
      <div class="person__role">President</div>
    </div>

    <div class="contact-icons">
      <svg viewBox="0 0 28 28" aria-label="Office phone">
        <rect width="28" height="28" fill="var(--brand-blue)"/>
        <path d="M7 11c0-3 3-4 7-4s7 1 7 4v2h-4v-2h-6v2H7z" fill="var(--paper)"/>
        <rect x="8" y="14" width="12" height="7" rx="1" fill="var(--paper)"/>
      </svg>
      <svg viewBox="0 0 28 28" aria-label="Mobile phone">
        <rect width="28" height="28" fill="var(--brand-blue)"/>
        <rect x="9.5" y="5" width="9" height="18" rx="1.5" fill="none" stroke="var(--paper)" stroke-width="1.8"/>
        <circle cx="14" cy="20" r="1" fill="var(--paper)"/>
      </svg>
      <svg viewBox="0 0 28 28" aria-label="Email">
        <rect width="28" height="28" fill="var(--brand-blue)"/>
        <rect x="6" y="8" width="16" height="12" fill="var(--paper)"/>
        <path d="M6 8l8 7 8-7" fill="none" stroke="var(--brand-blue)" stroke-width="1.5"/>
      </svg>
      <svg viewBox="0 0 28 28" aria-label="Website">
        <rect width="28" height="28" fill="var(--brand-blue)"/>
        <circle cx="14" cy="14" r="8" fill="none" stroke="var(--paper)" stroke-width="1.8"/>
        <ellipse cx="14" cy="14" rx="3.5" ry="8" fill="none" stroke="var(--paper)" stroke-width="1.4"/>
        <line x1="6" y1="14" x2="22" y2="14" stroke="var(--paper)" stroke-width="1.4"/>
      </svg>
    </div>

    <div class="contact-list">
      <div>214-555-0187</div>
      <div>000-000-9999</div>
      <div>info@example-youremail.com</div>
      <div>www.example-yourwebsite.com</div>
      <div class="divider"></div>
      <div class="address">482 Larkspur Ave, Ste<br>210, Dallas, TX 75204</div>
    </div>
  </section>

</main>
</body>
</html>
```